Process Serving Company needs a letterhead design

Looking to have a letterhead designed for letters to attorneys advertising our business. We would like something eye catching but professional. Colors and logos are attached. Please add "Process Service and Attorney Support" near the logo or header

Target Market(s)

Attorneys

Font styles to use
Serif
Sans Serif

Colors
33a6d7
0255a3
85cae6
cee9f5
ecf7fb

```html
<!DOCTYPE html>
<html lang="en">
<head>
<meta charset="utf-8">
<title>Mesa Point Serve Letterhead</title>
<link href="https://fonts.googleapis.com/css2?family=Open+Sans:wght@400;600;700&display=swap" rel="stylesheet">
<style>
  :root {
    --blue: #33a6d7;
    --navy: #0255a3;
    --sky: #85cae6;
    --mist: #cee9f5;
    --ice: #ecf7fb;
    --ink: #2b2b2b;
    --backdrop: #e9e9e9;
    --paper: #ffffff;
  }
  * { box-sizing: border-box; margin: 0; padding: 0; }
  html, body {
    width: 1200px; height: 918px; overflow: hidden;
    background: var(--backdrop);
    font-family: "Open Sans", sans-serif;
  }
  .letterhead {
    position: absolute; left: 267px; top: 24px;
    width: 666px; height: 870px;
    background: var(--paper);
    box-shadow: 0 6px 24px rgba(0,0,0,.12);
    overflow: hidden;
  }
  .brand {
    position: absolute; left: 52px; top: 50px;
    display: flex; align-items: center; gap: 10px;
  }
  .brand-mark { width: 22px; height: 22px; background: var(--blue); }
  .brand-name {
    font-size: 24px; font-weight: 600; color: var(--blue);
    letter-spacing: .5px;
  }
  .contact {
    position: absolute; right: 40px; top: 44px;
    display: flex; gap: 16px;
    font-size: 8px; line-height: 1.45; color: var(--ink);
  }
  .contact-company { color: var(--blue); font-weight: 600; }
  .contact-lines { list-style: none; }
  .contact-lines li { display: flex; align-items: center; gap: 5px; }
  .contact-icon {
    width: 9px; height: 9px; border-radius: 2px; background: var(--blue);
    display: inline-flex; align-items: center; justify-content: center;
  }
  .letter {
    position: absolute; left: 64px; top: 170px; width: 500px;
    font-size: 11.5px; line-height: 1.5; color: var(--ink);
  }
  .salutation { font-weight: 700; font-size: 13px; margin-bottom: 14px; }
  .letter p { margin-bottom: 14px; }
  .signature {
    width: 130px; height: 60px; margin-top: 6px;
    background: var(--ice); border-radius: 4px;
  }
  .swoosh { position: absolute; left: 0; top: 0; }
  .swoosh-text { font-size: 10px; fill: #fff; letter-spacing: .4px; }
</style>
</head>
<body>
<main class="letterhead">
  <header>
    <div class="brand">
      <span class="brand-mark"></span>
      <span class="brand-name">Mesa Point Serve</span>
    </div>
    <div class="contact">
      <address class="contact-address" style="font-style:normal">
        <div class="contact-company">Mesa Point Serve</div>
        4410 E Canyon Rd Ste 210<br>Mesa AZ 85201
      </address>
      <ul class="contact-lines">
        <li><span class="contact-icon"><svg width="6" height="6" viewBox="0 0 10 10"><path d="M2 1l2 2-1 1.5c.8 1.5 2 2.7 3.5 3.5L8 7l2 2-1.5 1C4 10 0 6 1 1.5z" fill="#fff"/></svg></span>480-555-0142</li>
        <li><span class="contact-icon"><svg width="6" height="6" viewBox="0 0 10 10"><path d="M2 1l2 2-1 1.5c.8 1.5 2 2.7 3.5 3.5L8 7l2 2-1.5 1C4 10 0 6 1 1.5z" fill="#fff"/></svg></span>480-555-0187</li>
        <li><span class="contact-icon"><svg width="6" height="6" viewBox="0 0 10 10"><path d="M1 2h8v6H1zM1 2l4 3 4-3" fill="none" stroke="#fff" stroke-width="1.2"/></svg></span>hello@mesapointserve.com</li>
      </ul>
    </div>
  </header>

  <section class="letter">
    <p class="salutation">Dear Mr. Harlan,</p>
    <p>Lorem Ipsum is simply dummy text of the printing and typesetting industry. Lorem Ipsum has been the industry's standard dummy text ever since the 1500s, when an unknown printer took a galley of type and scrambled it to make a type specimen book. It has survived not only five centuries, but also the leap into electronic typesetting, remaining essentially unchanged.</p>
    <p>The standard chunk of Lorem Ipsum used since the 1500s is reproduced below for those interested. Sections 1.10.32 and 1.10.33 from "de Finibus Bonorum et Malorum" by Marcellus are also reproduced in their exact original form, accompanied by English versions from the 1914 translation by T. Wexley.</p>
    <p>Lorem Ipsum is simply dummy text of the printing and typesetting industry. Lorem Ipsum has been the industry's standard dummy text ever since the 1500s, when an unknown printer took a galley of type and scrambled it to make a type specimen book. It has survived not only five centuries, but also the leap into electronic typesetting, remaining essentially unchanged. It was popularised in the</p>
    <p>Lorem Ipsum is simply dummy text of the printing and typesetting industry. Lorem Ipsum has been the industry's standard dummy text ever since the 1500s, when an unknown printer took a galley of type and scrambled it to make a type specimen book. It has survived not only five centuries, but also the leap into electronic typesetting, remaining essentially unchanged. It was popularised in the</p>
    <div class="signature" role="img" aria-label="Handwritten signature"></div>
  </section>

  <svg class="swoosh" width="666" height="870" viewBox="0 0 666 870" aria-hidden="true">
    <defs>
      <path id="swoosh-line" d="M390 860 Q560 730 652 530"/>
    </defs>
    <path d="M340 870 Q540 720 666 470 L666 478 Q548 730 360 870 Z" fill="var(--sky)"/>
    <path d="M370 870 Q560 730 666 500 L666 870 Z" fill="var(--blue)"/>
    <text class="swoosh-text"><textPath href="#swoosh-line" startOffset="38%">4410 E Canyon Rd Ste 210, Mesa AZ 85201</textPath></text>
  </svg>
</main>
</body>
</html>
```